July 2022 Industrial Manufacturer Product Expo Mexico City

We manufacture large screws and fastners for large Mining equipment, Trains, large ships, airplanes, wind turbines, and so on. We also do custom work base on the customer needs. No matter the size we can make it.
We have a Expo coming up with companies all over the world. We have to stand out we are a family own business so our customer service will be above and beyond anyone can provide. We do not have a sales force to push our products and services we provide one on one service.
Plus@!! I'm looking for anything that you designers can come up with if it was your company to put on a business card, plus i want to do a 1 or 2 sided pamphlet, and then a website. We make Speciality Bolts for large mining equipment these bolts can be 3 to 4 foot long!!! Plus fasteners, Nuts, washers, any, size, strengths, special materials, we offer more of a ono on one customer service, We are a small company, family own, but can fulfill any type of orders. We can also provide special time lines for emergency orders. "We keep the machines running we here at KRV don't believe in down time" We want to hear any slogan based on our company to stand out.
Thanks i really appreciate all your work and options that we have to pick on. Plus just a thought we could possibly want to entertain a experience Marketing internet help maybe a employment possibility. Thanks

I need 2 cards one in Spanish and English Like the steel back ground maybe send me in some bright red and blue writing Same with the Black cards Please remove the word Military The logo KRV maybe integrate a picture of a Bolt 🔩 Thank you

Still looking for I need 2 cards one in Spanish and English Like the steel back ground maybe send me in some bright red and blue writing Same with the Black cards try bright writing Please remove the word Military The logo KRV maybe integrate a picture of a Bolt 🔩 Plus will need the company to make a brochure and website next Thank you

Target Market(s)

Large Mining, Ship, Train, Green Energy, VELM, and Government equipment. Throughout the World

Industry/Entity Type

We can Custom Manufacture any type of Fastners for Mining equipment, Trains, Ships, Green energy, Governments, or military projects. wind turbines,

Contact Information for Business Card

I attached the name and contact info that's on a card, plus the Company Logo. Would like industrial looking background with Bright Colors that will stand out!! If we can insert somewhere maybe on back that we "Custom Manufacture Any Size or Quantity Fastners for Large Mining Equipment, Trains, Ships, Green Energy Equipment or Government Projects

Font styles to use
Other font styles liked:
• You Pick, has to be bold, colorful standout, Professional looking Beable to read it.

Colors

Designer to choose colors to be used in the design.

Requirements
Must have
• Need in Spanish and English TO STANDOUT FROM THE REST OF THE EXPO!! See Business card details, Rounded corners
Nice to have
• Can i see some of the darker cards with Bright Red and Blue letters I like to see the different type of card material, heavy thickness, plastic, transparent, Metal types, Bright Colors, I saw like Raised letters like on the logo.

```html
<!DOCTYPE html>
<html lang="es">
<head>
<meta charset="utf-8">
<title>KRV – Tarjetas de presentación / Business cards</title>
<link rel="stylesheet" href="https://fonts.googleapis.com/css2?family=Roboto+Condensed:ital,wght@0,400;0,700;1,700&family=Roboto:wght@400;500&display=swap">
<style>
  :root {
    --stage: #3b3f3b;
    --card-dark: #1e1f21;
    --card-steel: #2e3134;
    --brand-blue: #1b9cff;
    --brand-red: #ff2d2d;
    --text-light: #f2f2f2;
    --text-muted: #b9bec4;
    --logo-steel: #8d949b;
  }
  * { margin: 0; padding: 0; box-sizing: border-box; }
  html, body { width: 902px; height: 1200px; overflow: hidden; }
  body {
    background: var(--stage);
    position: relative;
    font-family: "Roboto", Arial, sans-serif;
  }
  .card {
    position: absolute;
    left: 71px;
    width: 760px;
    height: 434px;
    border-radius: 14px;
    overflow: hidden;
    box-shadow: 0 18px 40px rgba(0,0,0,0.45);
    background:
      repeating-linear-gradient(90deg, rgba(255,255,255,0.025) 0 1px, rgba(0,0,0,0) 1px 3px),
      linear-gradient(135deg, var(--card-steel) 0%, var(--card-dark) 45%, var(--card-steel) 70%, var(--card-dark) 100%);
  }
  .card--front { top: 74px; }
  .card--back { top: 692px; }
  .card__edge {
    position: absolute;
    left: 0; right: 0; bottom: 0;
    height: 6px;
    background: linear-gradient(90deg, var(--brand-blue) 0 50%, var(--brand-red) 50% 100%);
  }

  .contact {
    position: absolute;
    left: 62px;
    top: 130px;
    color: var(--text-light);
  }
  .contact__name {
    font-family: "Roboto Condensed", Arial, sans-serif;
    font-weight: 700;
    font-style: italic;
    font-size: 30px;
    color: var(--brand-blue);
    letter-spacing: 0.2px;
  }
  .contact__role {
    font-size: 17px;
    margin-top: 4px;
  }
  .contact__role-en { color: var(--brand-red); font-weight: 500; }
  .contact__rule {
    width: 28px;
    height: 3px;
    background: var(--brand-red);
    margin: 10px 0 14px;
  }
  .contact__list { list-style: none; }
  .contact__item {
    display: flex;
    align-items: center;
    gap: 10px;
    font-size: 17px;
    line-height: 26px;
  }
  .contact__icon { width: 15px; height: 15px; flex: none; }

  .brand {
    position: absolute;
    inset: 0;
    display: flex;
    flex-direction: column;
    align-items: center;
    justify-content: center;
  }
  .brand__name {
    display: flex;
    align-items: center;
    gap: 22px;
    font-family: "Roboto Condensed", Arial, sans-serif;
    font-weight: 700;
    font-size: 140px;
    line-height: 1;
    color: var(--logo-steel);
    letter-spacing: 8px;
  }
  .brand__dot {
    width: 32px; height: 32px;
    border-radius: 50%;
    background: var(--brand-red);
  }
  .brand__tagline {
    font-family: "Roboto Condensed", Arial, sans-serif;
    text-transform: uppercase;
    letter-spacing: 0.5px;
  }
  .brand__tagline--es {
    margin-top: 14px;
    font-weight: 400;
    font-size: 29px;
    color: var(--brand-blue);
  }
  .brand__tagline--en {
    margin-top: 6px;
    font-weight: 700;
    font-size: 21px;
    color: var(--brand-red);
  }
</style>
</head>
<body>
  <section class="card card--front">
    <div class="contact">
      <h1 class="contact__name">Lic. Marisol Ortega Vidal</h1>
      <p class="contact__role">Cotizaciones en · <span class="contact__role-en">Quotes at</span></p>
      <div class="contact__rule"></div>
      <ul class="contact__list">
        <li class="contact__item">
          <svg class="contact__icon" viewBox="0 0 16 16"><path fill="#1b9cff" d="M3.6 1.2l2.3 2.6-1.2 1.9c.9 2 2.6 3.7 4.6 4.6l1.9-1.2 2.6 2.3-1.3 2.6C7 13.9 2.1 9 1 3.3z"/></svg>
          <span>5550123481</span>
        </li>
        <li class="contact__item">
          <svg class="contact__icon" viewBox="0 0 16 16"><rect x="3.5" y="1" width="9" height="14" rx="1.5" fill="none" stroke="#1b9cff" stroke-width="1.6"/></svg>
          <span>5550198762</span>
        </li>
        <li class="contact__item">
          <svg class="contact__icon" viewBox="0 0 16 16"><rect x="1" y="3" width="14" height="10" fill="#1b9cff"/><path d="M1 3l7 6 7-6" fill="none" stroke="#1e1f21" stroke-width="1.4"/></svg>
          <span>ventas.krvtornillos@example.com</span>
        </li>
      </ul>
    </div>
    <div class="card__edge"></div>
  </section>

  <section class="card card--back">
    <div class="brand">
      <div class="brand__name"><span>KRV</span><span class="brand__dot"></span></div>
      <p class="brand__tagline brand__tagline--es">Fabricacion y distribucion de tornillos</p>
      <p class="brand__tagline brand__tagline--en">Bolt manufacturing &amp; distribution</p>
    </div>
    <div class="card__edge"></div>
  </section>
</body>
</html>
```